Business card design Needed for new logo / Construction business, home extensions and new builds

We need a business card design using our new logo files which i will attach to this project :)

We are a small construction business specialising in home extensions, new builds and property development. We are very ambitious and would appreciate professional and elegant designs for our new business card.

Very serious about using the services on MakerQuarry and recently acquired our new logo from here :)

Please get involved, i will feedback when i can as i am very busy but can respond daily, thanks

Target Market(s)

People that want to build onto their houses, new building developments or adding too their existing property

Industry/Entity Type

Construction

Contact Information for Business Card

Renwick Tolliver Construction, Lionel Ashby (Managing Director), Tel 07822254961, email - info@renwick-tolliver, www.renwick-tolliver.co.uk

Colors

Designer to choose colors to be used in the design.

Requirements
Must have
• I like a deep grey on the back please. A lot of you have provided black from and back, try mixing things up a little. The black looks cool 😎 Thanks

```html
<!DOCTYPE html>
<html lang="en">
<head>
<meta charset="utf-8">
<title>Renwick Tolliver Construction – Business Card</title>
<link rel="stylesheet" href="https://fonts.googleapis.com/css2?family=Open+Sans:wght@400;600;700&display=swap">
<style>
  :root {
    --backdrop: #222223;
    --card-dark: #242428;
    --card-dark-mid: #1f1f23;
    --card-dark-low: #1a1a1d;
    --card-grey: #717374;
    --grey-ink: #5a5c5e;
    --gold: #d9a23a;
    --gold-light: #f2c25e;
    --silver: #c9cbcd;
    --white: #f4f4f4;
    --icon-ink: #2a2418;
  }
  * { box-sizing: border-box; margin: 0; padding: 0; }
  html, body {
    width: 1200px; height: 780px; overflow: hidden;
    background: var(--backdrop);
    font-family: "Open Sans", Arial, sans-serif;
  }
  .stage {
    position: relative; width: 1200px; height: 780px;
    display: flex; justify-content: center; align-items: center; gap: 90px;
  }
  .card {
    position: relative; width: 340px; height: 525px;
    border-radius: 22px; overflow: hidden;
    box-shadow: 0 18px 40px rgba(0,0,0,.55);
  }

  /* Back: deep grey with brand name */
  .card--back { background: var(--card-grey); }
  .back-brand {
    position: absolute; left: 50%; top: 50%;
    transform: translate(-50%, -50%) rotate(-90deg);
    display: flex; align-items: center; gap: 14px;
    white-space: nowrap;
  }
  .back-brand__mark {
    width: 34px; height: 34px; background: var(--grey-ink);
  }
  .back-brand__name {
    font-weight: 600; font-size: 21px; letter-spacing: 2px;
    color: var(--grey-ink); text-transform: uppercase; line-height: 1.25;
  }

  /* Front: dark with contact details */
  .card--front { background: var(--card-dark); }
  .front-bands { position: absolute; inset: 0; }
  .front-content { position: absolute; inset: 0; text-align: center; }
  .brand {
    position: absolute; top: 62px; left: 0; right: 0;
    display: flex; flex-direction: column; align-items: center; gap: 12px;
  }
  .brand__mark {
    width: 46px; height: 46px; border-radius: 50%; background: var(--gold);
  }
  .brand__name {
    font-weight: 600; font-size: 15px; letter-spacing: 2.5px;
    color: var(--gold); text-transform: uppercase; line-height: 1.45;
  }
  .person {
    position: absolute; top: 212px; left: 0; right: 0;
  }
  .person__name { font-weight: 700; font-size: 27px; line-height: 1.1; }
  .person__first { color: var(--silver); }
  .person__last { color: var(--gold); }
  .person__role { margin-top: 3px; font-size: 13px; color: var(--white); font-weight: 600; }
  .contact-icons {
    position: absolute; top: 276px; left: 0; right: 0;
    display: flex; justify-content: center; gap: 8px;
  }
  .icon-dot {
    width: 22px; height: 22px; border-radius: 50%;
    background: radial-gradient(circle at 35% 30%, var(--gold-light), var(--gold));
    display: flex; align-items: center; justify-content: center;
  }
  .icon-dot svg { width: 12px; height: 12px; }
  .contact-list {
    position: absolute; top: 308px; left: 0; right: 0;
    list-style: none; font-size: 12.5px; line-height: 1.45; color: var(--white);
  }
  .address {
    position: absolute; bottom: 38px; left: 0; right: 0;
    display: flex; flex-direction: column; align-items: center; gap: 8px;
    font-size: 13px; line-height: 1.4; color: var(--white);
  }
</style>
</head>
<body>
<main class="stage">

  <section class="card card--back" aria-label="Card back">
    <div class="back-brand">
      <span class="back-brand__mark"></span>
      <span class="back-brand__name">Renwick Tolliver<br>Construction</span>
    </div>
  </section>

  <section class="card card--front" aria-label="Card front">
    <svg class="front-bands" viewBox="0 0 340 525" preserveAspectRatio="none" aria-hidden="true">
      <path d="M0 300 L0 525 L340 525 L340 300 Q300 410 130 418 Q40 420 0 380 Z" fill="var(--card-dark-mid)"/>
      <path d="M0 420 Q150 520 340 330 L340 525 L0 525 Z" fill="var(--card-dark-low)" opacity=".9"/>
      <path d="M340 300 Q300 410 130 418 Q40 420 0 380" fill="none" stroke="#121214" stroke-width="2" opacity=".6"/>
    </svg>

    <div class="front-content">
      <div class="brand">
        <span class="brand__mark"></span>
        <span class="brand__name">Renwick Tolliver<br>Construction</span>
      </div>

      <div class="person">
        <p class="person__name"><span class="person__first">Lionel</span> <span class="person__last">Ashby</span></p>
        <p class="person__role">Managing Director</p>
      </div>

      <div class="contact-icons">
        <span class="icon-dot" aria-label="Phone">
          <svg viewBox="0 0 24 24"><path fill="var(--icon-ink)" d="M6.6 10.8a15 15 0 0 0 6.6 6.6l2.2-2.2c.3-.3.7-.4 1-.2 1.1.4 2.3.6 3.6.6.6 0 1 .4 1 1V20c0 .6-.4 1-1 1A17 17 0 0 1 3 4c0-.6.4-1 1-1h3.5c.6 0 1 .4 1 1 0 1.3.2 2.5.6 3.6.1.3 0 .7-.2 1z"/></svg>
        </span>
        <span class="icon-dot" aria-label="Email">
          <svg viewBox="0 0 24 24"><path fill="var(--icon-ink)" d="M3 5h18v14H3z M4.5 6.5 12 12l7.5-5.5" stroke="var(--gold)" stroke-width="1.6"/></svg>
        </span>
        <span class="icon-dot" aria-label="Website">
          <svg viewBox="0 0 24 24"><circle cx="12" cy="12" r="9" fill="var(--icon-ink)"/><path d="M3 12h18M12 3c3 3 3 15 0 18M12 3c-3 3-3 15 0 18" stroke="var(--gold)" stroke-width="1.4" fill="none"/></svg>
        </span>
      </div>

      <ul class="contact-list">
        <li>0782 225 4961</li>
        <li>info@renwick-tolliver.co.uk</li>
        <li>www.renwick-tolliver.co.uk</li>
      </ul>

      <div class="address">
        <span class="icon-dot" aria-label="Location">
          <svg viewBox="0 0 24 24"><path fill="var(--icon-ink)" d="M12 2a7 7 0 0 0-7 7c0 5 7 13 7 13s7-8 7-13a7 7 0 0 0-7-7zm0 9.5A2.5 2.5 0 1 1 12 6.5a2.5 2.5 0 0 1 0 5z"/></svg>
        </span>
        <p>Harrow Lane, Westbrook<br>Fenmouth, FM4 2QT</p>
      </div>
    </div>
  </section>

</main>
</body>
</html>
```